Moxy Fen needs some awesome stationary

Do you have what it takes to get my brand? You either do or you don't, have a crack at a design and you my just win my business.

I don't want to waste your or my time, so put your creative genius on either a business card or envelope.

I however need a package of stationary that follows the same brand. I will message you to complete the remaining should I like your first submission.

Here is what I need, have a go!

Basically I need the following for my small business based in melbourne.
- Letterhead (printer ready and MS Word)
- Business Card
- Compliments Slip
- Envelope
- Proposal Cover Page (MS Word only)
- Presentation Folder
- Marbled Fox Cards
- Student Name Tent
- Index Cards
- Vell-Ka

I am establishing the brand and it must be modern, professional but also relaxed; that is not formal and not corporate. It represents a company are leaders, but small enough to care and operate like a bunch of friends. We are bringing people and conversations back to business, and turfing out all the bureaucracy and crazy and wasteful procedures. Its about "lets talk and figure it out together and find even better ways".

Target Market(s)

Mainly companies that build software products, but Agile practices are used in many other industries (even graphic design projects)

Industry/Entity Type

Information Technology

Font styles to use
Sans Serif

Colors
3176b5
aaaaaa

Requirements
Must have
• I like curves and circles and not boxes or rectangles.
• I want a colour rich design with my brand colours, but it must be balanced.
• I want more modern than traditional, but simple modern
Should not have
• Not corporate
• Please don't waste my time if your not going to think about it.
• Don't mess with my primary logo
• Don't change my colours
• Don't overlay logo on image

```html
<!DOCTYPE html>
<html lang="en">
<head>
<meta charset="utf-8">
<title>Moxy Fen — Business Card</title>
<link rel="stylesheet" href="https://fonts.googleapis.com/css2?family=PT+Sans:wght@400;700&display=swap">
<style>
  :root {
    --brand-blue: #2d5ca2;
    --brand-grey: #949fae;
    --ink: #333840;
    --card-white: #ffffff;
    --backdrop: #e8e6e3;
  }
  * { box-sizing: border-box; margin: 0; padding: 0; }
  html, body {
    width: 1200px; height: 987px; overflow: hidden;
    background: var(--backdrop);
    font-family: "PT Sans", sans-serif;
  }
  .canvas { position: relative; width: 1200px; height: 987px; }

  .card {
    position: absolute; left: 293px; width: 614px; height: 350px;
    box-shadow: 0 3px 10px rgba(0,0,0,0.18);
  }
  .card--front { top: 131px; background: var(--card-white); }
  .card--back { top: 506px; background: var(--brand-blue); }

  .front__tab {
    position: absolute; left: 0; top: 74px; width: 14px; height: 48px;
    background: var(--brand-blue); border-radius: 0 24px 24px 0;
  }
  .front__name {
    position: absolute; left: 33px; top: 72px;
    font-size: 22px; font-weight: 700; color: var(--brand-blue);
  }
  .front__role {
    position: absolute; left: 35px; top: 99px;
    font-size: 16px; color: var(--brand-grey);
  }
  .front__address {
    position: absolute; left: 36px; top: 129px;
    font-size: 16px; line-height: 22px; color: var(--ink);
    font-style: normal;
  }
  .front__contacts {
    position: absolute; left: 36px; top: 203px; list-style: none;
    font-size: 16px; color: var(--ink);
  }
  .front__contacts li {
    display: flex; align-items: center; height: 23.5px;
  }
  .front__contacts svg { width: 15px; height: 15px; margin-right: 8px; fill: var(--brand-blue); }

  .brand-lockup {
    position: absolute; display: flex; flex-direction: column; align-items: center;
  }
  .brand-lockup--front { left: 318px; top: 88px; width: 240px; }
  .brand-lockup__dot {
    width: 132px; height: 132px; border-radius: 50%; background: var(--brand-blue);
  }
  .brand-lockup__name {
    margin-top: 16px; font-size: 46px; font-weight: 700; line-height: 1;
    color: var(--brand-blue);
  }

  .brand-lockup--back { left: 378px; top: 216px; width: 200px; }
  .brand-lockup--back .brand-lockup__dot {
    width: 58px; height: 58px; background: var(--card-white);
  }
  .brand-lockup--back .brand-lockup__name {
    margin-top: 6px; font-size: 18px; color: var(--card-white);
  }
  .back__web {
    position: absolute; left: 378px; width: 200px; top: 301px; text-align: center;
    font-size: 16px; color: var(--card-white);
  }
</style>
</head>
<body>
<main class="canvas">
  <section class="card card--front" aria-label="Business card front">
    <span class="front__tab"></span>
    <h1 class="front__name">Dana Kestrel</h1>
    <p class="front__role">CEO, Professional Agile Trainer</p>
    <address class="front__address">
      PO Box 4471<br>Larkfield Vale<br>VIC 3190, Australia
    </address>
    <ul class="front__contacts">
      <li>
        <svg viewBox="0 0 16 16" aria-hidden="true"><path d="M3.6 1.2l2.3 2.9-1.3 1.8c.9 2 2.5 3.6 4.5 4.5l1.8-1.3 2.9 2.3-1.2 2.3C7.2 13.4 2.6 8.8 1.3 2.4z"/></svg>
        1300MOXYF
      </li>
      <li>
        <svg viewBox="0 0 16 16" aria-hidden="true"><path d="M4.5 0.5h7a1 1 0 0 1 1 1v13a1 1 0 0 1-1 1h-7a1 1 0 0 1-1-1v-13a1 1 0 0 1 1-1zM5 2.5v9.5h6V2.5zM8 12.8a.9.9 0 1 0 0 1.8.9.9 0 0 0 0-1.8z"/></svg>
        +61 400 217 386
      </li>
      <li>
        <svg viewBox="0 0 16 16" aria-hidden="true"><path d="M1 3.5h14v9H1zM2.3 4.5L8 9l5.7-4.5z" fill-rule="evenodd"/></svg>
        dana@moxyfen.com.au
      </li>
      <li>
        <svg viewBox="0 0 16 16" aria-hidden="true"><path d="M8 1a7 7 0 1 0 0 14A7 7 0 0 0 8 1zm-1 2.4c-.6.8-1.8 1.3-1.8 2.5 0 1 1.2 1 1.6 1.8.3.7-.4 1.6.2 2.3.5.6 1 1.8.9 2.7A5.4 5.4 0 0 1 2.7 7.2c1 .2 1.7-.6 2-1.4.4-1 1.2-1.8 2.3-2.4zm3.2 1c.8 0 1.8 1.2 2.4 2.3-.6.4-1.4.1-1.8.7-.5.7.2 1.8-.3 2.6-.4.7-1.4.6-1.6-.2-.2-.9.6-1.6.4-2.5-.2-.8-1-1.2-.9-2 .1-.6 1-.9 1.8-.9z"/></svg>
        www.moxyfen.com.au
      </li>
    </ul>
    <div class="brand-lockup brand-lockup--front">
      <span class="brand-lockup__dot"></span>
      <span class="brand-lockup__name">Moxy Fen</span>
    </div>
  </section>

  <section class="card card--back" aria-label="Business card back">
    <div class="brand-lockup brand-lockup--back">
      <span class="brand-lockup__dot"></span>
      <span class="brand-lockup__name">Moxy Fen</span>
    </div>
    <p class="back__web">www.moxyfen.com.au</p>
  </section>
</main>
</body>
</html>
```